BVM Marketing Postcard

Design a 2 Sided marketing postcard for our Real estate management caompany. Looking for a professional yet fresh look that will be printed on a 6"x9" glossy flier

Contact information is www.brixleymanagement.example brixleymanagement@postwellmail.example and 555-014-7283

WE are targeting small condo and town home properties to take on their administrative responsibilities of management

```html
<!DOCTYPE html>
<html lang="en">
<head>
<meta charset="utf-8">
<title>Brixley Property Services Postcard</title>
<link href="https://fonts.googleapis.com/css2?family=Montserrat:wght@400;500;600;700;800&display=swap" rel="stylesheet">
<style>
  :root {
    --navy: #1f2f5e;
    --slate: #4a5a87;
    --white: #ffffff;
    --ink: #223366;
    --photo-light: #d9d9d9;
    --photo-dark: #6f6f6f;
  }
  * { box-sizing: border-box; margin: 0; padding: 0; }
  html, body { width: 1200px; height: 1200px; overflow: hidden; background: var(--white); }
  body { font-family: "Montserrat", sans-serif; position: relative; }

  .card { position: absolute; left: 197px; width: 766px; }
  .card-front { top: 39px; height: 517px; }
  .card-back { top: 585px; height: 518px; }

  /* Front */
  .front-photo {
    position: absolute; left: 0; top: 0; width: 390px; height: 517px;
    background: linear-gradient(135deg, var(--photo-light) 0%, #a9a9a9 45%, var(--photo-dark) 100%);
  }
  .call-box {
    position: absolute; left: 106px; top: 224px; width: 237px; height: 112px;
    background: var(--ink); padding: 7px;
  }
  .call-box-inner {
    border: 3px solid var(--white); height: 100%; color: var(--white);
    text-align: center; display: flex; flex-direction: column; justify-content: center;
  }
  .call-label { font-size: 29px; font-weight: 500; letter-spacing: 1px; line-height: 1.1; }
  .call-number { font-size: 29px; font-weight: 700; line-height: 1.2; }

  .front-panel {
    position: absolute; left: 390px; top: 0; width: 376px; height: 517px;
    background: linear-gradient(180deg, var(--slate) 0%, #45558a 100%);
    color: var(--white); text-align: center;
  }
  .headline-small { margin-top: 33px; font-size: 13px; font-weight: 800; letter-spacing: .3px; }
  .headline-main { margin-top: 10px; font-size: 15px; font-weight: 800; letter-spacing: .3px; }
  .headline-sub { margin-top: 10px; font-size: 13.5px; font-weight: 500; }

  .brand { color: var(--white); text-align: center; }
  .brand-name { font-weight: 700; letter-spacing: 1px; line-height: 1; }
  .brand-line { display: flex; align-items: center; justify-content: center; gap: 8px; font-weight: 700; }
  .brand-dot { width: 10px; height: 10px; border-radius: 50%; background: var(--white); display: inline-block; }
  .front-panel .brand { margin-top: 22px; }
  .front-panel .brand-name { font-size: 34px; }
  .front-panel .brand-line { margin-top: 12px; font-size: 12px; }

  .benefit-box {
    position: absolute; left: 11px; top: 233px; width: 348px; height: 211px;
    border: 3px solid var(--white); padding: 12px 6px;
    display: flex; flex-direction: column; justify-content: space-between;
  }
  .benefit-box p { font-size: 11.3px; font-weight: 600; line-height: 1.25; }

  .price-line {
    position: absolute; left: 0; right: 0; top: 475px; font-size: 11px; font-weight: 700;
  }
  .price-line::before, .price-line::after {
    content: ""; position: absolute; left: 133px; width: 104px; height: 2px; background: var(--white);
  }
  .price-line::before { top: -8px; }
  .price-line::after { top: 22px; }
  .price-line small { font-size: 8.5px; font-weight: 500; }
  .price-line strong { font-size: 15px; font-weight: 800; }

  /* Back */
  .back-header {
    position: absolute; left: 0; top: 0; width: 766px; height: 70px; background: var(--navy);
    display: flex; align-items: center; justify-content: center;
  }
  .back-header .brand-name { font-size: 27px; }
  .back-header .brand-line { margin-top: 6px; font-size: 9px; }
  .header-rule { position: absolute; left: 0; top: 73px; width: 766px; height: 3px; background: var(--slate); }

  .col-left {
    position: absolute; left: 0; top: 76px; width: 384px; height: 388px; overflow: hidden;
    background: var(--slate); color: var(--white); padding: 18px 15px 0 26px;
  }
  .col-right {
    position: absolute; left: 384px; top: 76px; width: 382px; height: 388px; overflow: hidden;
    background: var(--white); color: var(--ink); padding: 18px 22px 0 13px;
  }
  .section-tag {
    display: inline-block; border: 2px solid currentColor; padding: 6px 6px;
    font-size: 13.5px; font-weight: 800; letter-spacing: .5px; line-height: 1.2;
  }
  .col-left .section-tag { border-color: var(--white); }
  .col-right .section-tag { border-color: var(--ink); }
  .col-left p, .col-right p { font-size: 13px; line-height: 1.18; text-align: justify; }
  .who p { margin-top: 13px; } .who p:first-of-type { margin-top: 12px; }
  .why { margin-top: 14px; }
  .why p { margin-top: 14px; } .why p:first-of-type { margin-top: 16px; }
  .col-right p { margin-top: 13px; font-weight: 500; }
  .col-right p:first-of-type { margin-top: 24px; }

  .back-footer {
    position: absolute; left: 0; top: 464px; width: 766px; height: 54px; background: var(--navy);
    color: var(--white); display: flex; align-items: center; justify-content: center;
    gap: 14px; font-size: 13px; font-weight: 600; white-space: nowrap;
  }
</style>
</head>
<body>
  <section class="card card-front">
    <div class="front-photo" role="img" aria-label="Black and white photo of a modern apartment building with stacked balconies"></div>
    <div class="call-box">
      <div class="call-box-inner">
        <span class="call-label">CALL</span>
        <span class="call-number">555-014-7283</span>
      </div>
    </div>
    <div class="front-panel">
      <p class="headline-small">COST EFFECTIVE</p>
      <p class="headline-main">PROPERTY MANAGEMENT SOLUTION</p>
      <p class="headline-sub">for 3-10 unit buildings</p>
      <div class="brand">
        <div class="brand-name">BRIXLEY</div>
        <div class="brand-line"><span>PROPERTY</span><span class="brand-dot"></span><span>SERVICES</span></div>
      </div>
      <div class="benefit-box">
        <p>Utilize our economies of scale to reduce costs across existing services (trash, insurance, maintenance, etc)</p>
        <p>Eliminate the unfair burden placed on a few owners to do all the work while others free-ride</p>
        <p>Improve communication amongst all owners</p>
        <p>The association's board of directors maintain all decision making power</p>
        <p>Utilize our vetted service providers for prompt job completion and fair pricing</p>
      </div>
      <p class="price-line">Prices starting <small>as low as</small> <strong>$ 100</strong>/<small>month</small></p>
    </div>
  </section>

  <section class="card card-back">
    <header class="back-header">
      <div class="brand">
        <div class="brand-name">BRIXLEY</div>
        <div class="brand-line"><span>PROPERTY</span><span class="brand-dot"></span><span>SERVICES</span></div>
      </div>
    </header>
    <div class="header-rule"></div>
    <div class="col-left">
      <div class="who">
        <span class="section-tag">WHO WE ARE</span>
        <p>A professional services organization with a focus on small (3-10 unit) residential buildings.</p>
        <p>Over 30 years of combined experience in real estate and property management.</p>
        <p>Professional, courteous, timely service that is technologically driven</p>
      </div>
      <div class="why">
        <span class="section-tag">WHY USE US?</span>
        <p>Owners are rarely suited to manage associations and the burden often falls unfairly on one or two individuals to do all the work.</p>
        <p>Low monthly fees tailored to your needs.</p>
        <p>The Association's board of directors maintains control of all decision making.</p>
      </div>
    </div>
    <div class="col-right">
      <span class="section-tag">WHAT WE DO</span>
      <p>Remove the administrative burden of managing small residential buildings</p>
      <p>Utilize economies of scale to reduce expense for all owners across a wide variety of services.</p>
      <p>Collect all assessments and pay all bills</p>
      <p>Provide access to BVM's client portal with central repository of all association materials (by-laws, financials, meeting minutes, communications etc)</p>
      <p>Issue 1099's to all contractors as required by law</p>
      <p>Prepare monthly accounting reconciliations &amp; year-end financial statements</p>
      <p>Lender and legal HOA documents for mortgage companies and sales.</p>
    </div>
    <footer class="back-footer">
      <span>www.brixleymanagement.example</span><span>|</span>
      <span>brixleymanagement@postwellmail.example</span><span>|</span>
      <span>555-014-7283</span>
    </footer>
  </section>
</body>
</html>
```